BildeVOLD buisnesscard

Hey :) I need a modern buisnesscard for my company BildeVOLD
It most have:
Dagligleder og Fotograf: Henrik Audun Strandvik

Mob: +4791264085
Epost: post@bildevold.example
Adresse: Kvernbakken9, 6040 Langevåg

Facbook and instagram logo with text BildeVOLD

BildeVOLD logo

It Company

```html
<!DOCTYPE html>
<html lang="no">
<head>
<meta charset="utf-8">
<title>BildeVOLD – visittkort</title>
<link href="https://fonts.googleapis.com/css2?family=Hind:wght@400;500;600;700&display=swap" rel="stylesheet">
<style>
  :root {
    --stage: #3b3b3b;
    --card-white: #ffffff;
    --brand-blue: #2580b5;
    --brand-pink: #c73a80;
    --ink: #555555;
    --rule: #8a8a8a;
    --on-blue: #ffffff;
  }
  * { margin: 0; padding: 0; box-sizing: border-box; }
  html, body {
    width: 1105px;
    height: 1200px;
    overflow: hidden;
    background: var(--stage);
    font-family: "Hind", Arial, sans-serif;
  }
  .canvas { position: relative; width: 1105px; height: 1200px; }

  .card {
    position: absolute;
    left: 193px;
    width: 720px;
    height: 410px;
    overflow: hidden;
  }

  /* Front */
  .card--front { top: 167px; background: var(--card-white); }
  .brand-name {
    position: absolute;
    right: 46px;
    top: 118px;
    font-size: 40px;
    font-weight: 700;
    line-height: 1;
    color: var(--brand-blue);
  }
  .holder { position: absolute; left: 44px; top: 225px; }
  .holder__name {
    font-size: 26px;
    font-weight: 600;
    color: var(--brand-blue);
    line-height: 1.2;
  }
  .holder__role {
    font-size: 20px;
    font-weight: 400;
    color: var(--brand-pink);
    line-height: 1.3;
  }
  .divider {
    position: absolute;
    left: 44px;
    right: 46px;
    top: 300px;
    height: 1px;
    background: var(--rule);
  }
  .contact, .address {
    position: absolute;
    top: 316px;
    font-size: 19px;
    line-height: 29px;
    color: var(--ink);
    list-style: none;
  }
  .contact { left: 44px; }
  .contact li { display: flex; align-items: center; gap: 10px; }
  .contact svg { width: 16px; height: 18px; fill: var(--brand-blue); flex: none; }
  .address { right: 46px; text-align: right; }

  /* Back */
  .card--back { top: 623px; background: var(--brand-blue); }
  .back-title {
    position: absolute;
    left: 566px;
    top: 40px;
    height: 345px;
    width: 56px;
    writing-mode: vertical-rl;
    transform: rotate(180deg);
    text-align: center;
    font-size: 52px;
    font-weight: 700;
    line-height: 56px;
    color: var(--on-blue);
  }
  .social-rail {
    position: absolute;
    left: 634px;
    top: 70px;
    width: 36px;
    height: 290px;
  }
</style>
</head>
<body>
<main class="canvas">

  <section class="card card--front" aria-label="Visittkort forside">
    <div class="brand-name">BildeVOLD</div>

    <div class="holder">
      <p class="holder__name">Henrik Audun Strandvik</p>
      <p class="holder__role">Dagligleder og Fotograf</p>
    </div>

    <div class="divider"></div>

    <ul class="contact">
      <li>
        <svg viewBox="0 0 16 18" aria-hidden="true"><path d="M3 0h10a1.5 1.5 0 0 1 1.5 1.5v15A1.5 1.5 0 0 1 13 18H3a1.5 1.5 0 0 1-1.5-1.5v-15A1.5 1.5 0 0 1 3 0zm0.5 2.5v11h9v-11zm4.5 12.3a1 1 0 1 0 0.01 0z"/></svg>
        <span>+4791264085</span>
      </li>
      <li>
        <svg viewBox="0 0 16 18" aria-hidden="true"><path d="M0 5h16v10H0zm1.5 1.5v0.4L8 11l6.5-4.1v-0.4z"/></svg>
        <span>post@bildevold.example</span>
      </li>
    </ul>

    <address class="address" style="font-style:normal">
      Kvernbakken9<br>6040 Langevåg
    </address>
  </section>

  <section class="card card--back" aria-label="Visittkort bakside">
    <div class="back-title">BildeVOLD</div>
    <svg class="social-rail" viewBox="0 0 36 290" aria-hidden="true">
      <g fill="none" stroke="var(--on-blue)" stroke-width="1.2">
        <line x1="18" y1="0" x2="18" y2="96"/>
        <circle cx="18" cy="116" r="16"/>
        <circle cx="18" cy="165" r="16"/>
        <line x1="18" y1="186" x2="18" y2="290"/>
      </g>
    </svg>
  </section>

</main>
</body>
</html>
```